Yard sign

Looking for a yard sign. <br/>Something simple, name, number. <br/>Large text, readable from 50 feet away. <br/><br/>18 x 24 inches.

Target Market(s)

Potential homeowners thinking about going solar.

Colors

Designer to choose colors to be used in the design.

Requirements
Must have
• "WE'VE GONE SOLAR!"
Nice to have
• We are a solar company, we would like a design that compliments the homeowners decision that they went solar and encourages others to do the same.

```html
<!DOCTYPE html>
<html lang="en">
<head>
<meta charset="utf-8">
<title>We've Gone Solar Yard Sign</title>
<link rel="stylesheet" href="https://fonts.googleapis.com/css2?family=Bebas+Neue&family=Montserrat:wght@700;800&display=swap">
<style>
  :root {
    --backdrop: #231f20;
    --header-orange: #e35205;
    --header-glow: #f8a50d;
    --band-orange: #f4760b;
    --sun-yellow: #f8b510;
    --sign-white: #ffffff;
    --ink: #111111;
    --headline-shadow: #4a1a04;
  }
  html, body {
    margin: 0;
    width: 1200px;
    height: 1200px;
    overflow: hidden;
    background: var(--backdrop);
  }
  .yard-sign {
    position: absolute;
    left: 48px;
    top: 163px;
    width: 1103px;
    height: 827px;
    display: block;
  }
  .headline {
    font-family: "Bebas Neue", "Oswald", sans-serif;
    font-size: 190px;
  }
  .headline-text { fill: var(--sign-white); }
  .headline-shadow { fill: var(--headline-shadow); }
  .brand-name {
    font-family: "Montserrat", sans-serif;
    font-weight: 800;
    font-size: 44px;
    fill: var(--band-orange);
  }
  .phone-number {
    font-family: "Montserrat", sans-serif;
    font-weight: 700;
    font-size: 124px;
    fill: var(--sign-white);
  }
  .rep-name {
    font-family: "Montserrat", sans-serif;
    font-weight: 700;
    font-size: 44px;
    fill: var(--ink);
  }
</style>
</head>
<body>
<svg class="yard-sign" viewBox="0 0 1103 827" xmlns="http://www.w3.org/2000/svg" role="img" aria-label="Yard sign: We've gone solar! Hudson Sun Power, 555 214 7368, Marcus Reilly">
  <defs>
    <radialGradient id="header-glow" cx="830" cy="20" r="420" gradientUnits="userSpaceOnUse">
      <stop offset="0" style="stop-color: var(--header-glow)"/>
      <stop offset="1" style="stop-color: var(--header-orange)"/>
    </radialGradient>
    <linearGradient id="fold-shade" x1="0" y1="0" x2="1" y2="0">
      <stop offset="0" stop-color="#b0b0b0"/>
      <stop offset="0.5" stop-color="#e2e2e2"/>
      <stop offset="1" stop-color="#b0b0b0"/>
    </linearGradient>
  </defs>

  <rect class="sign-face" width="1103" height="827" fill="var(--sign-white)"/>

  <polygon class="header-fold" points="0,234 553,283 1103,234 1103,243 553,309 0,243" fill="url(#fold-shade)"/>
  <polygon class="header-band" points="0,0 1103,0 1103,234 553,283 0,234" fill="url(#header-glow)"/>

  <text class="headline headline-shadow" x="54" y="211" textLength="1006" lengthAdjust="spacingAndGlyphs">WE'VE GONE SOLAR!</text>
  <text class="headline headline-text" x="49" y="207" textLength="1006" lengthAdjust="spacingAndGlyphs">WE'VE GONE SOLAR!</text>

  <circle class="brand-dot" cx="290" cy="468" r="38" fill="var(--sun-yellow)"/>
  <text class="brand-name" x="350" y="484">HUDSON SUN POWER</text>

  <rect class="accent-rule" x="0" y="630" width="1103" height="11" fill="var(--band-orange)"/>
  <rect class="contact-band" x="0" y="645" width="1103" height="182" fill="var(--band-orange)"/>

  <text class="phone-number" x="552" y="754" text-anchor="middle" textLength="779" lengthAdjust="spacingAndGlyphs">555 214 7368</text>

  <path class="name-rule" d="M204,788 Q270,785 339,785 L339,791 Q270,791 204,788 Z" fill="var(--ink)"/>
  <path class="name-rule" d="M898,788 Q832,785 763,785 L763,791 Q832,791 898,788 Z" fill="var(--ink)"/>
  <text class="rep-name" x="551" y="807" text-anchor="middle" textLength="384" lengthAdjust="spacingAndGlyphs">MARCUS REILLY</text>
</svg>
</body>
</html>
```